Investment company needing business card

We are wanting a business card which looks sharp and easy on the eye. We are thinking of having a business card with the logo embossed on it, to really make it stand out. We will only have a small amount of information of the business card, person's name, position, email address and phone number

Contact Information for Business Card

Danielle Frost
Executive Assistant
+64 21 473 5162
danielf@harwickpartners.co.nz

Requirements
Must have
• Embossed logo
Should not have
• Not to be busy

```html
<!DOCTYPE html>
<html lang="en">
<head>
<meta charset="utf-8">
<title>Harwick Partners – Business Card</title>
<link rel="stylesheet" href="https://fonts.googleapis.com/css2?family=Lato:wght@400;900&display=swap">
<style>
  :root {
    --stage: #3a3a3c;
    --card-white: #ffffff;
    --card-dark: #262626;
    --card-dark-tone: #2e2e2e;
    --brand-green: #20b26b;
    --brand-grey: #5f6062;
    --ink: #2b2b2b;
    --rule: #8a8a8a;
  }
  * { box-sizing: border-box; margin: 0; padding: 0; }
  html, body {
    width: 1200px; height: 1108px; overflow: hidden;
    background: var(--stage);
    font-family: "Lato", Arial, sans-serif;
  }
  .sheet {
    position: relative; width: 1200px; height: 1108px;
    display: flex; flex-direction: column; align-items: center;
    justify-content: center; gap: 48px;
  }
  .card {
    position: relative; width: 840px; height: 480px;
    box-shadow: 0 18px 40px rgba(0,0,0,.35);
  }
  .card--front { background: var(--card-white); }
  .card--back { background: var(--card-dark); overflow: hidden; }

  .contact {
    position: absolute; left: 64px; top: 200px;
    color: var(--ink);
  }
  .contact__name {
    font-weight: 900; font-size: 30px; letter-spacing: 2px;
    text-transform: uppercase; color: var(--brand-green);
  }
  .contact__role { font-size: 22px; margin-top: 4px; }
  .contact__list { list-style: none; margin-top: 20px; font-size: 20px; }
  .contact__list li { display: flex; align-items: center; gap: 12px; margin-top: 6px; }
  .contact__list svg { width: 18px; height: 18px; fill: var(--brand-green); flex: none; }

  .wordmark {
    display: flex; align-items: center; gap: 16px;
    font-weight: 900; color: var(--brand-green);
    text-transform: uppercase; letter-spacing: 4px;
  }
  .wordmark__square { background: var(--brand-grey); flex: none; }
  .card--front .wordmark {
    position: absolute; right: 64px; top: 70px; font-size: 36px;
  }
  .card--front .wordmark__square { width: 44px; height: 44px; }
  .card--front .divider {
    position: absolute; right: 64px; top: 132px; width: 420px;
    height: 2px; background: var(--rule);
  }

  .back-texture {
    position: absolute; inset: 0;
    background: linear-gradient(135deg, var(--card-dark-tone), var(--card-dark));
  }
  .card--back .wordmark {
    position: absolute; left: 50%; top: 50%; transform: translate(-50%, -50%);
    font-size: 40px;
  }
  .card--back .wordmark__square { width: 48px; height: 48px; }
</style>
</head>
<body>
<main class="sheet">
  <section class="card card--front" aria-label="Card front">
    <div class="wordmark"><span class="wordmark__square"></span>Harwick Partners</div>
    <div class="divider"></div>
    <div class="contact">
      <p class="contact__name">Danielle Frost</p>
      <p class="contact__role">Executive Assistant</p>
      <ul class="contact__list">
        <li>
          <svg viewBox="0 0 24 24" aria-hidden="true"><path d="M6.6 10.8a15 15 0 0 0 6.6 6.6l2.2-2.2a1 1 0 0 1 1-.25 11.4 11.4 0 0 0 3.6.57 1 1 0 0 1 1 1V20a1 1 0 0 1-1 1A17 17 0 0 1 3 4a1 1 0 0 1 1-1h3.5a1 1 0 0 1 1 1c0 1.25.2 2.45.57 3.6a1 1 0 0 1-.25 1z"/></svg>
          +64 21 473 5162
        </li>
        <li>
          <svg viewBox="0 0 24 24" aria-hidden="true"><path d="M2 5h20v14H2zm2 2v.5l8 5 8-5V7zm0 2.8V17h16V9.8l-8 5z"/></svg>
          danielf@harwickpartners.co.nz
        </li>
      </ul>
    </div>
  </section>

  <section class="card card--back" aria-label="Card back">
    <div class="back-texture" role="img" aria-label="Subtle tone-on-tone repeating brand pattern"></div>
    <div class="wordmark"><span class="wordmark__square"></span>Harwick Partners</div>
  </section>
</main>
</body>
</html>
```